Manufacturer's Representative Group needs a clean new Website

We represent and sell a number of suppliers that design and build products used in Biopharmaceutical manufacturing. Our sales region is in the central US. Our customer base is scientific / engineering based - so clean, we organized design with a focus on the products - easy and clear navigation is necessary. We do not sell direct or warehouse product - so e-commerce is not needed. Our customers will use the website for reference on what we do and offer - we will use the site as a platform to present products from each vendor and the home page will be used to capture an overview and draw users deeper into the site. You can view our current site - which needs A LOT of help to get ideas on products represented and types of products

Target Market(s)

Engineers and Pharmaceutical / Bio pharm end users

Industry/Entity Type

E-Commerce

Number of Pages Required

2 page

Font styles to use
Sans Serif

Requirements
Must have
• I need a home page that provides a snapshot of my company and the product lines we represent - then a second page that I can copy as a template for each line I rep as well as for an "About us / contact" page.
• I would like to be able to manage content on the pages so something easy to adjust pictures or add content is a must
• Must use our logo

```html
<!DOCTYPE html>
<html lang="en">
<head>
<meta charset="utf-8">
<title>Prairie Bio — Home</title>
<link href="https://fonts.googleapis.com/css2?family=Raleway:wght@500;600&family=Mulish:wght@700&family=Questrial&family=Oswald:wght@500&display=swap" rel="stylesheet">
<style>
  :root {
    --navy: #262262;
    --orange: #f15a24;
    --orange-light: #ff7a3d;
    --white: #ffffff;
    --panel-grey: #efefef;
    --text-dark: #222222;
    --text-muted: #444444;
    --rule: #cfcfcf;
    --field-border: #c4c4c4;
    --placeholder: #8a8a8a;
  }
  * { box-sizing: border-box; margin: 0; padding: 0; }
  html, body { width: 740px; height: 1200px; overflow: hidden; }
  body {
    position: relative;
    background: var(--navy);
    font-family: Arial, Helvetica, sans-serif;
    color: var(--text-dark);
  }
  .abs { position: absolute; }

  /* Header */
  .site-header { left: 0; top: 0; width: 740px; height: 67px; background: var(--white); }
  .header-rule { left: 0; top: 67px; width: 740px; height: 3px; background: var(--orange); }
  .brand { left: 62px; top: 20px; display: flex; align-items: center; gap: 8px; }
  .brand-dot { width: 22px; height: 22px; border-radius: 50%; background: var(--orange); }
  .brand-name {
    font-family: "Raleway", sans-serif; font-weight: 600; font-size: 26px;
    color: var(--navy); letter-spacing: -0.3px;
  }
  .main-nav { left: 428px; top: 38px; display: flex; height: 29px; }
  .main-nav a {
    display: block; height: 29px; line-height: 29px; text-decoration: none;
    font-family: "Raleway", sans-serif; font-weight: 500; font-size: 12.5px; color: var(--text-dark);
  }
  .main-nav .is-active { width: 71px; text-align: center; background: var(--orange); color: var(--white); border-radius: 2px 2px 0 0; }
  .main-nav .nav-contact { margin-left: 17px; }
  .main-nav .nav-products { margin-left: 37px; }

  /* Content panel */
  .content-panel { left: 62px; top: 80px; width: 616px; height: 707px; background: var(--white); }

  .hero { left: 65px; top: 84px; width: 610px; height: 254px; overflow: hidden; }
  .hero-media {
    width: 100%; height: 100%;
    background: linear-gradient(180deg, #e9ecf1 0%, #cfd5de 60%, #aab1bd 100%);
  }
  .hero-caption {
    left: 0; bottom: 0; width: 100%; height: 37px; background: rgba(20,20,20,.82);
    color: var(--white); font-family: "Raleway", sans-serif; font-weight: 500; font-size: 15px;
    line-height: 37px; padding-left: 16px;
  }

  .section-title {
    left: 0; width: 740px; text-align: center;
    font-family: "Mulish", sans-serif; font-weight: 700; font-size: 16px; color: var(--orange);
  }
  .double-rule { height: 5px; border-top: 1px solid var(--rule); border-bottom: 1px solid var(--rule); }

  .intro-title { top: 355px; }
  .intro-rule { left: 173px; top: 378px; width: 371px; }
  .intro-copy {
    left: 78px; top: 396px; width: 585px; text-align: center;
    font-size: 10.5px; line-height: 14.8px; color: var(--text-dark);
  }

  .products-title { top: 490px; }
  .products-rule { left: 281px; top: 515px; width: 175px; }

  .product-card {
    top: 550px; width: 134px; height: 197px; border: 1px solid #d6d6d6; background: var(--white); padding: 3px;
  }
  .product-media { width: 100%; height: 93px; }
  .product-copy {
    margin-top: 12px; padding: 0 2px; text-align: center;
    font-family: "Questrial", sans-serif; font-size: 9px; line-height: 12.4px; color: var(--text-muted);
  }
  .card-1 { left: 68px; }  .card-2 { left: 226px; }
  .card-3 { left: 379px; } .card-4 { left: 533px; }
  .media-tubing { background: linear-gradient(150deg, #6c7c8e 0%, #a7b3bf 45%, #2c3645 100%); }
  .media-pump-blue { background: linear-gradient(160deg, #e3e7ec 0%, #3c66a8 50%, #8c8f93 100%); }
  .media-pump-red { background: linear-gradient(160deg, #d9d2c6 0%, #c0262b 55%, #8f8a80 100%); }
  .media-cleanroom { background: linear-gradient(180deg, #eef0f2 0%, #c9ced3 60%, #9aa1a8 100%); }

  /* Contact */
  .contact-panel { left: 62px; top: 787px; width: 616px; height: 334px; background: var(--panel-grey); }
  .contact-title { top: 807px; }
  .contact-rule { left: 177px; top: 833px; width: 371px; }
  .field {
    left: 213px; width: 296px; height: 28px; background: var(--white);
    border: 1px solid var(--field-border); border-radius: 3px;
    font-family: Arial, sans-serif; font-size: 10px; color: var(--text-dark); padding: 0 8px;
  }
  .field::placeholder { color: var(--placeholder); }
  .field-first { top: 853px; } .field-last { top: 892px; } .field-email { top: 935px; }
  .field-message { top: 974px; height: 76px; padding-top: 8px; resize: none; }
  .submit-button {
    left: 417px; top: 1067px; width: 91px; height: 24px; border: 0; border-radius: 3px;
    background: linear-gradient(180deg, var(--orange-light) 0%, var(--orange) 60%, #d9481a 100%);
    color: var(--white); font-family: "Oswald", sans-serif; font-weight: 500; font-size: 13px; letter-spacing: 1.5px;
  }

  /* Footer */
  .site-footer { left: 62px; top: 1121px; width: 616px; height: 58px; background: var(--orange); color: var(--white); }
  .footer-nav { left: 15px; top: 14px; display: flex; font-size: 10px; }
  .footer-nav a { color: var(--white); text-decoration: none; }
  .footer-nav .sep { margin: 0 17px; }
  .copyright { left: 15px; top: 32px; font-size: 10px; }
  .footer-brand { left: 440px; top: 14px; display: flex; align-items: center; gap: 7px; }
  .footer-brand .brand-dot { background: var(--white); width: 20px; height: 20px; }
  .footer-brand .brand-name { color: var(--white); font-size: 23px; }
</style>
</head>
<body>
  <header class="abs site-header">
    <div class="abs brand"><span class="brand-dot"></span><span class="brand-name">Prairie Bio</span></div>
    <nav class="abs main-nav">
      <a class="is-active" href="#">HOME</a>
      <a class="nav-contact" href="#">Contact Us</a>
      <a class="nav-products" href="#">Products</a>
    </nav>
  </header>
  <div class="abs header-rule"></div>

  <main>
    <div class="abs content-panel"></div>

    <section class="abs hero">
      <div class="hero-media" role="img" aria-label="Photo of laboratory glassware holding coloured liquids"></div>
      <p class="abs hero-caption">We offer these in standard and custom configurations!</p>
    </section>

    <h2 class="abs section-title intro-title">PR-Bio Now Representing Keystone Fluidics!</h2>
    <div class="abs double-rule intro-rule"></div>
    <p class="abs intro-copy">Prairie Biosolutions is a distribution channel, licensed partner and manufacturers representative group providing high quality fluid handling products and technical services to the Midwestern biopharmaceutical community. With a core staff of experienced professionals and a team approach to all customer needs, we offer over 30 years of cGMP experience in the selection and use of most process consumable products. We're looking forward to working with you!</p>

    <h2 class="abs section-title products-title">Our Products</h2>
    <div class="abs double-rule products-rule"></div>

    <article class="abs product-card card-1">
      <div class="product-media media-tubing" role="img" aria-label="Single-use tubing assemblies and fittings"></div>
      <p class="product-copy">Concept, design and production of single use assemblies, custom carboys, tubing manifolds and other products designed for cGMP applications</p>
    </article>
    <article class="abs product-card card-2">
      <div class="product-media media-pump-blue" role="img" aria-label="Blue peristaltic pump with tubing"></div>
      <p class="product-copy">Concept, design and production of single use assemblies, custom carboys, tubing manifolds and other products designed for cGMP applications</p>
    </article>
    <article class="abs product-card card-3">
      <div class="product-media media-pump-red" role="img" aria-label="Red benchtop peristaltic pump with digital display"></div>
      <p class="product-copy">Concept, design and production of single use assemblies, custom carboys, tubing manifolds and other products designed for cGMP applications</p>
    </article>
    <article class="abs product-card card-4">
      <div class="product-media media-cleanroom" role="img" aria-label="Cleanroom production area with suspended equipment"></div>
      <p class="product-copy">Concept, design and production of single use assemblies, custom carboys, tubing manifolds and other products designed for cGMP applications</p>
    </article>

    <section>
      <div class="abs contact-panel"></div>
      <h2 class="abs section-title contact-title">PR- Bio Contact Us</h2>
      <div class="abs double-rule contact-rule"></div>
      <input class="abs field field-first" type="text" placeholder="User Name">
      <input class="abs field field-last" type="text" placeholder="Last Name">
      <input class="abs field field-email" type="email" placeholder="Email Address">
      <textarea class="abs field field-message" placeholder="Message"></textarea>
      <button class="abs submit-button" type="button">SUBMIT</button>
    </section>
  </main>

  <footer class="abs site-footer">
    <nav class="abs footer-nav">
      <a href="#">Home</a><span class="sep">|</span><a href="#">Contact Us</a><span class="sep">|</span><a href="#">Products</a>
    </nav>
    <p class="abs copyright">© Prairie Biosolutions, Corp.</p>
    <div class="abs footer-brand"><span class="brand-dot"></span><span class="brand-name">Prairie Bio</span></div>
  </footer>
</body>
</html>
```